Business Card for Multi-Brand Sportswear Company

We are looking for a business card which represents our company and the multiple brands within it.

The company: Fen Athletics (LTD)
The brands: Fen, TavaPuni, ElmStretch, Grit and Rain

Employees using these cards would be representing Fen Athletics, rather than any of the individual brands. You will see a current design within the uploaded files, to give some inspiration. The actual text of the brands is not necessary, but the logos should be on there is some format.

Our creative minds on this are stretched, so we are looking for someone to make this their own, and show us what a good business card should look like.

We may like to get these printed with spot gloss, so keep that in mind with your designs.

www.fenathletics.co.uk

Industry/Entity Type

Business

Contact Information for Business Card

Leo Pemberton-Hale
Operations Manager
(+44) 1632 960 418
Leo@fenathletics.co.uk
www.fenathletics.co.uk

Font styles to use
Sans Serif
Other font styles liked:
• Eurostile

Colors
ffffff

Requirements
Nice to have
• Dark (black) background

```html
<!DOCTYPE html>
<html lang="en">
<head>
<meta charset="utf-8">
<title>Fen Athletics – Business Card</title>
<link rel="stylesheet" href="https://fonts.googleapis.com/css2?family=Quicksand:wght@400;500;600&display=swap">
<style>
  :root {
    --backdrop: #8a8a8a;
    --card-dark: #1f1f1f;
    --card-panel: #2b2929;
    --accent-red: #e0232a;
    --logo-grey: #7b7b7b;
    --text-white: #ffffff;
    --text-soft: #e6e6e6;
  }
  * { margin: 0; padding: 0; box-sizing: border-box; }
  html, body { width: 1200px; height: 854px; overflow: hidden; }
  body {
    background: var(--backdrop);
    font-family: "Quicksand", sans-serif;
    position: relative;
  }
  .card {
    position: absolute;
    top: 288px;
    width: 503px;
    height: 288px;
    background: var(--card-dark);
    box-shadow: 0 6px 18px rgba(0,0,0,0.35);
    overflow: hidden;
  }
  .card--front { left: 117px; }
  .card--back { left: 639px; }

  /* front */
  .front-brand {
    position: absolute;
    left: 0; top: 0;
    width: 266px; height: 100%;
  }
  .divider {
    position: absolute;
    left: 266px; top: 0;
    width: 2px; height: 100%;
    background: var(--accent-red);
  }
  .contact-panel {
    position: absolute;
    left: 268px; top: 0;
    width: 235px; height: 100%;
    background: var(--card-panel);
  }
  .person-name {
    position: absolute;
    right: 21px; top: 113px;
    font-size: 17px; font-weight: 600;
    color: var(--text-white);
    white-space: nowrap;
  }
  .person-role {
    position: absolute;
    right: 21px; top: 140px;
    font-size: 14px; font-weight: 500;
    color: var(--text-soft);
  }
  .contact-list { list-style: none; }
  .contact-item {
    position: absolute;
    right: 21px;
    font-size: 13px; font-weight: 500;
    color: var(--text-soft);
    white-space: nowrap;
    line-height: 18px;
  }
  .contact-item--phone { top: 191px; }
  .contact-item--email { top: 215px; }
  .contact-item--web { top: 238px; }
  .icon-tab {
    position: absolute;
    left: 0;
    width: 34px; height: 18px;
    background: var(--accent-red);
    border-radius: 0 3px 3px 0;
    display: flex; align-items: center; justify-content: center;
  }
  .icon-tab--phone { top: 191px; }
  .icon-tab--email { top: 215px; }
  .icon-tab--web { top: 238px; }
  .icon-tab svg { width: 11px; height: 11px; }

  /* logo lockup */
  .wordmark {
    position: absolute;
    color: var(--logo-grey);
    font-weight: 600;
    white-space: nowrap;
    letter-spacing: 0.5px;
    line-height: 1.2;
  }
  .tagline {
    position: absolute;
    color: var(--logo-grey);
    font-weight: 500;
    letter-spacing: 1.6px;
    white-space: nowrap;
    line-height: 1;
  }
  .brand-row {
    position: absolute;
    display: flex;
    align-items: center;
    white-space: nowrap;
    line-height: 1;
  }
  .brand-name {
    color: var(--text-soft);
    font-weight: 500;
  }

  .front-brand .wordmark { left: 18px; top: 106px; font-size: 28px; width: 237px; text-align: right; }
  .front-brand .tagline { right: 11px; top: 146px; font-size: 6.5px; }
  .front-brand .brand-row { left: 0; width: 266px; justify-content: center; top: 181px; gap: 12px; }
  .front-brand .brand-name { font-size: 10px; }

  .card--back .wordmark { left: 0; width: 503px; text-align: center; top: 100px; font-size: 48px; }
  .card--back .tagline { right: 45px; top: 160px; font-size: 11px; }
  .card--back .brand-row { left: 0; width: 503px; justify-content: center; top: 232px; gap: 18px; }
  .card--back .brand-name { font-size: 12px; }
</style>
</head>
<body>

  <section class="card card--front" aria-label="Business card front">
    <div class="front-brand">
      <div class="wordmark">Fen Athletics</div>
      <div class="tagline">PERFORMANCE WEAR</div>
      <div class="brand-row">
        <span class="brand-name">TavaPuni</span>
        <span class="brand-name">Grit and Rain</span>
        <span class="brand-name">Fen</span>
        <span class="brand-name">ElmStretch</span>
      </div>
    </div>
    <div class="divider"></div>
    <div class="contact-panel">
      <h1 class="person-name">Leo Pemberton-Hale</h1>
      <p class="person-role">Operations Manager</p>

      <span class="icon-tab icon-tab--phone">
        <svg viewBox="0 0 12 12"><path d="M2.5 1 L4.3 1 L5 3.3 L3.9 4.3 Q5 6.8 7.7 8.1 L8.7 7 L11 7.7 L11 9.5 Q11 11 9.5 11 Q1 10 1 2.5 Q1 1 2.5 1 Z" fill="#fff"/></svg>
      </span>
      <span class="icon-tab icon-tab--email">
        <svg viewBox="0 0 12 12"><rect x="1" y="2.5" width="10" height="7" fill="none" stroke="#fff" stroke-width="1.2"/><path d="M1 2.5 L6 6.5 L11 2.5" fill="none" stroke="#fff" stroke-width="1.2"/></svg>
      </span>
      <span class="icon-tab icon-tab--web">
        <svg viewBox="0 0 12 12" fill="none" stroke="#fff" stroke-width="1"><circle cx="6" cy="6" r="5"/><ellipse cx="6" cy="6" rx="2.2" ry="5"/><path d="M1 6 H11 M2 3.5 H10 M2 8.5 H10"/></svg>
      </span>

      <ul class="contact-list">
        <li class="contact-item contact-item--phone">(+44) 1632 960 418</li>
        <li class="contact-item contact-item--email">Leo@fenathletics.co.uk</li>
        <li class="contact-item contact-item--web">www.fenathletics.co.uk</li>
      </ul>
    </div>
  </section>

  <section class="card card--back" aria-label="Business card back">
    <div class="wordmark">Fen Athletics</div>
    <div class="tagline">PERFORMANCE WEAR</div>
    <div class="brand-row">
      <span class="brand-name">TavaPuni</span>
      <span class="brand-name">Grit and Rain</span>
      <span class="brand-name">Fen</span>
      <span class="brand-name">ElmStretch</span>
    </div>
  </section>

</body>
</html>
```